Classic and neutral book cover design

We are looking for a classic and neutral book cover design to be used as the template for a series of books to be published. We are hence looking for a template that will allow us to easily change the title name for all books in this series.
The use of very few colours (black and white is welcome) and few design elements is a big bonus. As a source of inspiration we would like to ask you to view the very simple and
If you think you have a cool idea that can add a twist to the formal classic look don't hesitate. Go for it !
Work will be done for a 30 year old Sweden based cultural non-profit called VĂ©ru (www.verufoundation.example). We work with the publishing and supporting of post-modern art and literature addressing contemporary topics but are also involved in assisting projects of cultural preservation.
Target Market(s)
The audience is expected to have some form of interest in culture but could range from hobbyist readers to tenure track scholars
Industry/Entity Type
Non-Profit
Requirements
Must have
- General:
- Classic and neutral feel
- Preferably very simple and few shapes
- usage of few colours (black and white is welcome)
Information to be displayed on the cover is:
- Author
- Title
- type of work e.g. play/novel (optional)
- publishing house (in this case "Veru Publishing")
Nice to have
- ideas to prevent it from become boring are of course welcome
Should not have
- - too many colours

```html
<!DOCTYPE html>
<html lang="en">
<head>
<meta charset="utf-8">
<title>Book Title – Véru Publishing</title>
<link href="https://fonts.googleapis.com/css2?family=Poiret+One&family=Raleway:wght@300;400&display=swap" rel="stylesheet">
<style>
  :root {
    --paper: #fdfaf3;
    --parchment: #f3e6c8;
    --parchment-deep: #d9b777;
    --frame-brown: #4a2a12;
    --title-maroon: #5a1a1c;
    --text-grey: #3a3a3a;
    --accent-orange: #f0a326;
    --publisher-ink: #1a1a1a;
  }
  html, body {
    margin: 0;
    padding: 0;
    width: 848px;
    height: 1200px;
    overflow: hidden;
    background: var(--paper);
  }
  .cover {
    position: relative;
    width: 848px;
    height: 1200px;
    overflow: hidden;
  }
  .cover__texture {
    position: absolute;
    inset: 0;
    background:
      radial-gradient(ellipse 62% 55% at 50% 45%, var(--paper) 0%, rgba(253,250,243,0.85) 45%, rgba(243,230,200,0.7) 75%, rgba(217,183,119,0.75) 100%),
      linear-gradient(180deg, var(--parchment) 0%, var(--paper) 40%, var(--paper) 60%, var(--parchment) 100%);
  }
  .cover__frame {
    position: absolute;
    inset: 0;
  }
  .cover__author {
    position: absolute;
    top: 148px;
    left: 0;
    width: 100%;
    text-align: center;
    font-family: "Raleway", sans-serif;
    font-weight: 300;
    font-size: 27px;
    letter-spacing: 0.5px;
    color: var(--text-grey);
    margin: 0;
  }
  .cover__title {
    position: absolute;
    top: 196px;
    left: 0;
    width: 100%;
    text-align: center;
    font-family: "Poiret One", sans-serif;
    font-weight: 400;
    font-size: 144px;
    line-height: 1;
    letter-spacing: 2px;
    color: var(--title-maroon);
    margin: 0;
  }
  .cover__genre {
    position: absolute;
    top: 354px;
    left: 182px;
    width: 476px;
    height: 45px;
    box-sizing: border-box;
    border: 2px dotted var(--accent-orange);
    display: flex;
    align-items: center;
    justify-content: center;
    font-family: "Raleway", sans-serif;
    font-weight: 300;
    font-size: 22px;
    color: var(--text-grey);
  }
  .cover__publisher {
    position: absolute;
    top: 1028px;
    left: 0;
    width: 100%;
    text-align: center;
    font-family: "Poiret One", sans-serif;
    font-weight: 400;
    font-size: 52px;
    letter-spacing: 3px;
    color: var(--publisher-ink);
    margin: 0;
  }
</style>
</head>
<body>
  <main class="cover">
    <div class="cover__texture" role="img" aria-label="Aged parchment texture with faint ink splashes and bare branches along the edges"></div>

    <svg class="cover__frame" width="848" height="1200" viewBox="0 0 848 1200" aria-hidden="true">
      <rect x="90" y="89" width="672" height="1029" fill="none"
            stroke="var(--frame-brown)" stroke-width="6"
            stroke-linecap="round" stroke-dasharray="0 11.8"/>
    </svg>

    <p class="cover__author">AUTHOR NAME</p>
    <h1 class="cover__title">Book Title</h1>
    <div class="cover__genre">roman</div>
    <p class="cover__publisher">VÉRU</p>
  </main>
</body>
</html>
```